Vortaleen - Lead the Way!

Vortaleen is a new Silicon Valley company, of the pimrela founders from Berlin, which provides a "Shared Hive Circle". This platform allows the crowd to support startups with money, experts and fame. Our Vision is, that everyone should become an entrepreneur.

Pls find all brief details in the attached document
Updates

Would be nice to have a list of more social services I'm available on, like a list of pictograms of all my services:

Find me on: chattro, fennwix+, qrt, mivrel, datebloom, pohk, rplex, etc...

pls make sure to use the right font:
http://www.typelarder-demo.com/fonts/Orbitron

Target Market(s)

Main target market is those already involved in the startup industry, by fundraising, investing, advising, cofounding and working. Vortaleen brings a totaly new transparency and collaborative way of starting companies to that business.

· Entrepreneurs (looking for funding, team and community)
· Investors (looking for hot investments and )
· Experts (workers looking for startups they can work for equity)
· Incubators & Business Schools (looking for tools to advise startups)

Industry/Entity Type

It Company

Requirements
Must have
• Pls find all brief details in the attached document
Nice to have

```html
<!DOCTYPE html>
<html lang="en">
<head>
<meta charset="utf-8">
<title>Vortaleen – Business Card</title>
<link href="https://fonts.googleapis.com/css2?family=Orbitron:wght@500;600&family=Open+Sans:wght@300;400;600&display=swap" rel="stylesheet">
<style>
  :root {
    --stage: #393634;
    --brand: #e35f3a;
    --paper: #ffffff;
    --ink: #5a5a5a;
    --label: #7a7773;
    --light: #ffffff;
  }
  * { margin: 0; padding: 0; box-sizing: border-box; }
  html, body { width: 840px; height: 1200px; overflow: hidden; background: var(--stage); }
  body { position: relative; font-family: "Open Sans", Arial, sans-serif; }

  .card { position: absolute; left: 100px; width: 645px; height: 373px; overflow: hidden; }
  .card--front { top: 197px; background: var(--paper); }
  .card--back { top: 665px; background: var(--brand); color: var(--light); text-align: center; }

  .band { position: absolute; left: 0; width: 100%; background: var(--brand); }
  .band--top { top: 0; height: 55px; }
  .band--bottom { bottom: 0; height: 53px; display: flex; align-items: center; justify-content: center; gap: 10px; padding-left: 8px; }

  .web-tab {
    position: absolute; left: 68px; top: 55px; width: 205px; height: 31px;
    background: var(--brand); border-radius: 0 0 10px 10px;
    color: var(--light); font-size: 13px; font-weight: 300; letter-spacing: .3px;
    display: flex; align-items: center; justify-content: center;
  }
  .side-tab { position: absolute; left: 0; top: 121px; width: 32px; height: 148px; background: var(--brand); border-radius: 0 10px 10px 0; }

  .holder { position: absolute; left: 87px; top: 130px; }
  .holder__name { font-family: "Orbitron", "Open Sans", sans-serif; font-weight: 600; font-size: 24px; letter-spacing: .6px; color: var(--brand); line-height: 1.1; }
  .holder__role { margin-top: 8px; font-size: 16px; font-weight: 400; letter-spacing: .5px; color: var(--ink); }

  .contact { position: absolute; left: 87px; top: 233px; font-size: 13px; font-weight: 300; line-height: 16px; color: var(--ink); }
  .contact__key { color: var(--brand); }

  .brand-mark { position: absolute; left: 415px; top: 205px; width: 165px; text-align: center; color: var(--ink); font-family: "Orbitron", "Open Sans", sans-serif; }
  .brand-mark__name { font-size: 23px; font-weight: 500; letter-spacing: .3px; line-height: 1; }
  .brand-mark__tagline { margin-top: 4px; font-size: 11px; font-weight: 500; }

  .social { display: flex; align-items: center; gap: 6px; color: var(--light); font-size: 10px; font-weight: 300; }
  .social__icon { width: 10px; height: 10px; background: var(--light); opacity: .85; border-radius: 1px; }

  .pitch { position: absolute; left: 0; top: 122px; width: 100%; }
  .pitch__question { font-size: 17px; font-weight: 600; }
  .pitch__join { font-size: 16px; font-weight: 300; margin-top: 0; }

  .divider { position: absolute; left: 120px; top: 286px; width: 402px; border-top: 1px dashed rgba(255,255,255,.7); }
  .addresses { position: absolute; left: 0; top: 308px; width: 100%; font-size: 11.5px; font-weight: 300; line-height: 14px; }

  .side-label { position: absolute; left: 0; width: 100%; text-align: center; color: var(--label); font-size: 14px; font-weight: 300; letter-spacing: .5px; }
  .side-label--front { top: 594px; }
  .side-label--back { top: 1070px; }
</style>
</head>
<body>

  <section class="card card--front" aria-label="Card front">
    <div class="band band--top"></div>
    <div class="web-tab">www.vortaleen.com</div>
    <div class="side-tab"></div>

    <div class="holder">
      <h1 class="holder__name">MAREK LINDQVIST</h1>
      <p class="holder__role">FOUNDER AND CEO</p>
    </div>

    <p class="contact">
      <span class="contact__key">email</span> the@vortaleen.com<br>
      <span class="contact__key">phone</span> 081 555 204 617
    </p>

    <div class="brand-mark">
      <p class="brand-mark__name">Vortaleen</p>
      <p class="brand-mark__tagline">Lead the Way!</p>
    </div>

    <div class="band band--bottom">
      <span class="social"><span class="social__icon"></span>chirpline.com/mareklindqvist</span>
      <span class="social"><span class="social__icon"></span>friendsy.com/mareklindqvist</span>
      <span class="social"><span class="social__icon"></span>workmesh.com/in/mareklindqvist</span>
    </div>
  </section>
  <p class="side-label side-label--front">FRONT</p>

  <section class="card card--back" aria-label="Card back">
    <div class="pitch">
      <p class="pitch__question">Are you interested in Startups, Investments, Work?</p>
      <p class="pitch__join">Join: Friendsy.com/Vortaleen</p>
    </div>
    <div class="divider"></div>
    <p class="addresses">
      Berlin - Lindenweg 12 . 10115 Berlin . Germany<br>
      Silicon Valley - 218 Orchard Ln . Sunnyvale . CA 94086
    </p>
  </section>
  <p class="side-label side-label--back">BACK</p>

</body>
</html>
```